Mara Penrith Copywriter Website

I am starting a new business as a freelance copywriter. Trying to set up the website for my business is proving to be too technical for me. I would like a simple, clean website using primarily black and white. I have attached the logo I would like used. I would like the menu icons to be Home, Services, Portfolio, Blog, Contact. I would like my mobile phone number (0412 583 906) and email address (mara.penrith.copywriter@fernmail.test) used in the header of the site. I need the site to be easily manageable and inter-changeable for me to be able to move things around and add images, etc with ease.

I would like the home page to be a static page with space for an image of myself somewhere (I haven't had this taken as yet), an area to put a bit about myself and my business, and also somewhere to include social media icons/links. Again, I would like the whole website and home page to be easily managed so that I can add/delete things with ease.

I would like the image of the typewriter used in the website somewhere also please.

Coding

Coded - Design and coding required

Number of Pages Required

5+ page

Font styles to use
Sans Serif
Script

Colors
fdf0f6

Requirements
Must have
• The logo provided
• Ability to change page contents easily
• Ability to add social media icons as needed
Nice to have
• Use of the typewriter image
Should not have
• Complicated pages that are not easily editable

```html
<!DOCTYPE html>
<html lang="en">
<head>
<meta charset="utf-8">
<title>Mara Penrith Copywriter</title>
<link href="https://fonts.googleapis.com/css2?family=Josefin+Sans:wght@300;400;600;700&family=Great+Vibes&display=swap" rel="stylesheet">
<style>
:root{
  --ink:#111111;
  --text:#444444;
  --muted:#8a8a8a;
  --paper:#ffffff;
  --mist:#f3f3f3;
  --line:#d9d9d9;
  --blush:#fdf0f6;
  --hero-a:#3d3d3f;
  --hero-b:#6b6b6d;
}
*{box-sizing:border-box;margin:0;padding:0}
html,body{width:1200px;height:3408px;overflow:hidden}
body{position:relative;background:var(--paper);color:var(--text);font-family:"Josefin Sans",Arial,sans-serif;font-size:17px;line-height:1.6}
.script{font-family:"Great Vibes",cursive;font-weight:400;color:var(--ink)}
.section-title{font-size:54px;text-align:center;line-height:1}
.btn{display:inline-block;background:var(--ink);color:#fff;font-weight:600;font-size:17px;padding:16px 30px;line-height:1}

/* header */
.topbar{position:absolute;top:0;left:0;width:1200px;height:112px}
.contact-item{position:absolute;top:30px;display:flex;gap:14px;align-items:center;font-size:15px;line-height:1.35;color:var(--ink)}
.contact-item small{display:block;color:var(--muted);font-size:14px}
.contact-item.phone{left:60px}
.contact-item.email{right:40px}
.icon-box{width:28px;height:28px;background:var(--ink);display:flex;align-items:center;justify-content:center}
.brand{position:absolute;left:450px;top:22px;width:300px;height:68px;display:flex;align-items:center;justify-content:center;gap:12px}
.brand-mark{width:16px;height:16px;background:var(--blush);border:1px solid #f3d3e2}
.brand-name{font-size:22px;font-weight:600;color:var(--ink);letter-spacing:1px}
.nav{position:absolute;top:112px;left:0;width:1200px;height:48px;border-top:1px solid var(--line);background:#fff}
.nav ul{list-style:none;display:flex;margin-left:60px;height:48px}
.nav li{padding:0 28px;display:flex;align-items:center;font-size:16px;color:var(--ink)}
.nav li.active{background:var(--ink);color:#fff}
.search{position:absolute;right:40px;top:0;width:48px;height:48px;background:var(--ink);display:flex;align-items:center;justify-content:center}

/* hero */
.hero{position:absolute;top:160px;left:0;width:1200px;height:552px;background:radial-gradient(ellipse at 40% 45%,var(--hero-b),var(--hero-a) 75%)}
.hero-frame{position:absolute;left:340px;top:72px;width:520px;height:368px;border:3px solid rgba(255,255,255,.75);text-align:center;color:#fff;padding-top:96px}
.hero-frame h1{font-size:56px;color:#fff;line-height:1}
.hero-frame p{width:380px;margin:22px auto 24px;font-size:16px;color:#eee}
.hero-frame .btn{border:2px solid #fff}

/* about */
.about{position:absolute;top:712px;left:0;width:1200px;height:456px}
.portrait-frame{position:absolute;left:80px;top:92px;width:230px;height:270px;border:12px solid var(--ink)}
.portrait{position:absolute;left:112px;top:60px;width:240px;height:300px;background:linear-gradient(160deg,#e9e4df,#b9a79a 60%,#3a2e2a)}
.about-body{position:absolute;left:520px;top:72px;width:560px}
.about-body h2{font-size:52px;line-height:1;margin-bottom:28px}
.about-body p{margin-bottom:22px}

/* services */
.services{position:absolute;top:1168px;left:0;width:1200px;height:520px;background:var(--mist)}
.services .section-title{margin-top:72px}
.services .lead{width:640px;margin:26px auto 0;text-align:center}
.service-grid{position:absolute;top:220px;left:60px;width:1080px;display:flex}
.service{flex:1;text-align:center}
.service-icon{width:72px;height:72px;margin:0 auto 20px;border:3px solid var(--ink);display:flex;align-items:center;justify-content:center;background:#fff}
.service h3{font-size:18px;font-weight:700;color:var(--ink);margin-bottom:6px}
.service p{width:200px;margin:0 auto;font-size:15px}

/* portfolio */
.portfolio{position:absolute;top:1688px;left:0;width:1200px;height:480px}
.portfolio .section-title{margin-top:40px}
.tiles{position:absolute;top:112px;left:0;width:1200px;height:288px;display:flex}
.tile{position:relative;width:300px;height:288px}
.tile .shot{position:absolute;inset:0}
.tile .label{position:absolute;left:0;bottom:0;width:100%;height:40px;background:var(--ink);color:#fff;font-weight:700;font-size:16px;text-align:center;line-height:44px}
.tile.raised{margin-top:-16px;height:320px;background:#fff;box-shadow:0 4px 18px rgba(0,0,0,.18)}
.tile.raised .shot{inset:0 0 64px 0}
.tile.raised .label{background:#fff;color:var(--ink);height:64px;line-height:68px}

/* news */
.news{position:absolute;top:2180px;left:0;width:1200px;height:460px;background:var(--mist)}
.news .section-title{margin-top:72px}
.news-grid{position:absolute;top:140px;left:72px;width:1056px;display:flex;justify-content:space-between}
.post{position:relative;width:500px;height:240px}
.post .shot{position:absolute;left:0;top:20px;width:260px;height:200px}
.post-card{position:absolute;left:200px;top:0;width:280px;height:240px;background:#fff;padding:26px 22px;box-shadow:0 3px 14px rgba(0,0,0,.1)}
.post-card h3{font-size:17px;font-weight:700;color:var(--ink);line-height:1.35}
.meta{display:flex;gap:18px;margin:12px 0;font-size:13px;color:var(--muted);border-bottom:3px solid var(--ink);width:46px;padding-bottom:10px;white-space:nowrap}
.meta span{display:flex;align-items:center;gap:5px}
.post-card p{font-size:15px;margin-top:14px}
.post-card .rule{width:50px;height:3px;background:var(--ink);margin-top:10px}

/* contact */
.contact{position:absolute;top:2640px;left:0;width:1200px;height:448px}
.contact .section-title{margin-top:80px}
.form{position:absolute;top:144px;left:272px;width:656px}
.row{display:flex;gap:16px;margin-bottom:16px}
.field{flex:1;height:40px;border:1px solid var(--line);padding:0 12px;font-size:14px;color:var(--muted);line-height:42px}
.field.active{border:2px solid var(--ink);color:var(--ink)}
.field.area{height:72px;line-height:32px}
.form .btn{margin-left:256px;padding:16px 40px}

/* footer */
.footer{position:absolute;top:3088px;left:0;width:1200px;height:320px;background:var(--ink);color:#fff;text-align:center}
.footer .brand{position:static;margin:28px auto 0;width:300px}
.footer .brand-name{color:#fff}
.footer-nav{margin-top:26px;font-size:16px}
.footer-nav span{margin:0 22px}
.socials{display:flex;justify-content:center;gap:14px;margin-top:30px}
.socials i{width:30px;height:30px;background:#fff;display:block}
.footer hr{border:0;border-top:1px solid #444;width:1060px;margin:30px auto 0}
.copyright{margin-top:22px;font-size:14px;color:#ddd}
</style>
</head>
<body>

<header class="topbar">
  <div class="contact-item phone">
    <span class="icon-box"><svg width="14" height="14" viewBox="0 0 24 24"><path fill="#fff" d="M6.6 10.8a15 15 0 006.6 6.6l2.2-2.2c.3-.3.7-.4 1-.2 1.1.4 2.3.6 3.6.6.6 0 1 .4 1 1V20c0 .6-.4 1-1 1A17 17 0 013 4c0-.6.4-1 1-1h3.5c.6 0 1 .4 1 1 0 1.3.2 2.5.6 3.6.1.3 0 .7-.2 1z"/></svg></span>
    <div><small>Phone</small>0412 583 906</div>
  </div>
  <div class="brand"><span class="brand-mark"></span><span class="brand-name">Mara Penrith Copywriter</span></div>
  <div class="contact-item email">
    <span class="icon-box"><svg width="14" height="12" viewBox="0 0 24 18"><path fill="none" stroke="#fff" stroke-width="2" d="M1 1h22v16H1zM1 1l11 9 11-9"/></svg></span>
    <div><small>E-mail</small>mara.penrith.copywriter@fernmail.test</div>
  </div>
</header>

<nav class="nav">
  <ul><li class="active">Home</li><li>Services</li><li>Portfolio</li><li>Blog</li><li>Contact</li></ul>
  <span class="search"><svg width="18" height="18" viewBox="0 0 24 24"><circle cx="10" cy="10" r="7" fill="none" stroke="#fff" stroke-width="2.5"/><path d="M15 15l7 7" stroke="#fff" stroke-width="2.5"/></svg></span>
</nav>

<section class="hero" role="img" aria-label="Desk with open notebook, pen and glasses in dark tones">
  <div class="hero-frame">
    <h1 class="script">Hi, I'm Mara Penrith</h1>
    <p>Lorem Ipsum is simply dummy text of the printing and typesetting industry. Lorem Ipsum since the 1500s.</p>
    <span class="btn">Contact Me</span>
  </div>
</section>

<section class="about">
  <div class="portrait-frame"></div>
  <div class="portrait" role="img" aria-label="Portrait of Mara Penrith holding a notebook"></div>
  <div class="about-body">
    <h2 class="script">About Mara Penrith</h2>
    <p>Lorem Ipsum is simply dummy text of the printing and typesetting industry. Lorem Ipsum has been the industry's standard dummy text ever since the 1500s, when an unknown printer took a galley of type and scramble type specimen book.</p>
    <p>It has survived not only five centuries, but also the leap into electronic typesetting, remaining essentially unchanged. It was versions of Lorem Ipsum.</p>
    <span class="btn">Read More</span>
  </div>
</section>

<section class="services">
  <h2 class="script section-title">Services</h2>
  <p class="lead">Lorem Ipsum is simply dummy text of the printing and typesetting industry. Lorem Ipsum has been the industry's standard dummy text ever since the 1500s.</p>
  <div class="service-grid">
    <div class="service">
      <div class="service-icon"><svg width="36" height="36" viewBox="0 0 36 36" fill="none" stroke="#111" stroke-width="2.5"><rect x="5" y="5" width="26" height="26"/><path d="M5 12h26M10 18h16M10 24h10"/></svg></div>
      <h3>Blogging</h3><p>Lorem Ipsum is simply dummy text typesetting industry.</p>
    </div>
    <div class="service">
      <div class="service-icon"><svg width="36" height="36" viewBox="0 0 36 36" fill="none" stroke="#111" stroke-width="2.5"><path d="M8 3h15l6 6v24H8z"/><path d="M13 14h11M13 20h11M13 26h8"/></svg></div>
      <h3>SEO Articles</h3><p>Lorem Ipsum is simply dummy text typesetting industry.</p>
    </div>
    <div class="service">
      <div class="service-icon"><svg width="36" height="36" viewBox="0 0 36 36" fill="none" stroke="#111" stroke-width="2.5"><rect x="4" y="6" width="28" height="20"/><path d="M12 26l-3 6 8-6M10 13h16M10 19h10"/></svg></div>
      <h3>Social Copywriting</h3><p>Lorem Ipsum is simply dummy text typesetting industry.</p>
    </div>
    <div class="service">
      <div class="service-icon"><svg width="36" height="36" viewBox="0 0 36 36" fill="none" stroke="#111" stroke-width="2.5"><rect x="5" y="5" width="26" height="26"/><rect x="10" y="10" width="8" height="8"/><path d="M21 11h5M21 17h5M10 23h16"/></svg></div>
      <h3>Press Release Writing</h3><p>Lorem Ipsum is simply dummy text typesetting industry.</p>
    </div>
  </div>
</section>

<section class="portfolio">
  <h2 class="script section-title">Portfolio</h2>
  <div class="tiles">
    <div class="tile"><div class="shot" role="img" aria-label="Hands turning pages of a document" style="background:linear-gradient(135deg,#d8d6d2,#7d7a76)"></div><div class="label">Lorem Ipsum</div></div>
    <div class="tile raised"><div class="shot" role="img" aria-label="Hands typing on a vintage typewriter" style="background:linear-gradient(180deg,#cfcfcf,#4a4a4a)"></div><div class="label">Lorem Ipsum</div></div>
    <div class="tile"><div class="shot" role="img" aria-label="Writer seated at a desk in a dark room" style="background:radial-gradient(circle at 50% 40%,#6b5e55,#151515 70%)"></div><div class="label">Lorem Ipsum</div></div>
    <div class="tile"><div class="shot" role="img" aria-label="Vintage typewriter with a sheet of paper" style="background:linear-gradient(160deg,#eeeeee,#8a8a8a)"></div><div class="label">Lorem Ipsum</div></div>
  </div>
</section>

<section class="news">
  <h2 class="script section-title">Recent News</h2>
  <div class="news-grid">
    <article class="post">
      <div class="shot" role="img" aria-label="Woman working at a typewriter" style="background:linear-gradient(135deg,#cfc9c4,#6f655e)"></div>
      <div class="post-card">
        <h3>Lorem Ipsum is simply dummy printing</h3>
        <div class="meta"><span><svg width="14" height="10" viewBox="0 0 24 16"><path d="M1 8s4-7 11-7 11 7 11 7-4 7-11 7S1 8 1 8z" fill="none" stroke="#888" stroke-width="2"/><circle cx="12" cy="8" r="3" fill="#888"/></svg>0</span><span><svg width="12" height="11" viewBox="0 0 24 22"><path d="M12 21S1 14 1 7a5.5 5.5 0 0111-2 5.5 5.5 0 0111 2c0 7-11 14-11 14z" fill="#888"/></svg>13</span><span><svg width="12" height="11" viewBox="0 0 24 22"><path d="M2 2h20v14H8l-6 5z" fill="none" stroke="#888" stroke-width="2"/></svg>0</span></div>
        <p>Lorem Ipsum is simply dummy text of the printing and typesetting industry.</p>
        <div class="rule"></div>
      </div>
    </article>
    <article class="post">
      <div class="shot" role="img" aria-label="Hands holding an open book" style="background:linear-gradient(135deg,#bdb8b3,#5a5551)"></div>
      <div class="post-card">
        <h3>Lorem Ipsum is simply dummy printing</h3>
        <div class="meta"><span><svg width="14" height="10" viewBox="0 0 24 16"><path d="M1 8s4-7 11-7 11 7 11 7-4 7-11 7S1 8 1 8z" fill="none" stroke="#888" stroke-width="2"/><circle cx="12" cy="8" r="3" fill="#888"/></svg>0</span><span><svg width="12" height="11" viewBox="0 0 24 22"><path d="M12 21S1 14 1 7a5.5 5.5 0 0111-2 5.5 5.5 0 0111 2c0 7-11 14-11 14z" fill="#888"/></svg>13</span><span><svg width="12" height="11" viewBox="0 0 24 22"><path d="M2 2h20v14H8l-6 5z" fill="none" stroke="#888" stroke-width="2"/></svg>0</span></div>
        <p>Lorem Ipsum is simply dummy text of the printing and typesetting industry.</p>
        <div class="rule"></div>
      </div>
    </article>
  </div>
</section>

<section class="contact">
  <h2 class="script section-title">Contact Me</h2>
  <div class="form">
    <div class="row"><div class="field active">Name*</div><div class="field">E-mail*</div></div>
    <div class="row"><div class="field">Phone*</div><div class="field">Subject</div></div>
    <div class="row"><div class="field area">Message</div></div>
    <span class="btn">Submit</span>
  </div>
</section>

<footer class="footer">
  <div class="brand"><span class="brand-mark"></span><span class="brand-name">Mara Penrith Copywriter</span></div>
  <div class="footer-nav"><span>Home</span>|<span>Services</span>|<span>Portfolio</span>|<span>Blog</span>|<span>Contact</span></div>
  <div class="socials"><i></i><i></i><i></i><i></i></div>
  <hr>
  <p class="copyright">© MARA PENRITH - 2018. All Rights Reserved</p>
</footer>

</body>
</html>
```